Business card for law firm

Need business card for new law firm. Think confident, authoritative, conservative, but not stuffy or old-fashioned.

Contact Information for Business Card

Content for card - logo (uploaded), plus the following:

Paul Whitcombe (larger font)
Managing Partner (larger font, but not as large as name)
Level 9, 7 Ferris Lane
Sydney NSW 2000
Main Tel 02 9364 2710
Direct Tel 02 8472 3159
Email paul@qvlegal.com.au
www.qvlegal.com.au

Letterhead design should include logo plus:
Level 9, 7 Ferris Lane
Sydney NSW 2000
Tel 02 8472 3159
www.qvlegal.com.au

```html
<!DOCTYPE html>
<html lang="en">
<head>
<meta charset="utf-8">
<title>Quayvale Legal – Business Card</title>
<link rel="stylesheet" href="https://fonts.googleapis.com/css2?family=Cinzel:wght@400&family=Roboto:wght@400;500;700&display=swap">
<style>
  :root {
    --navy: #0e1f5e;
    --navy-deep: #0a1748;
    --ink: #1a1a1a;
    --text: #2b2b2b;
    --paper: #ffffff;
    --backdrop: #e6e7ea;
  }
  * { box-sizing: border-box; margin: 0; padding: 0; }
  html, body {
    width: 1200px; height: 1000px; overflow: hidden;
    background: var(--backdrop);
    font-family: "Roboto", Arial, sans-serif;
  }
  .card {
    position: absolute; left: 240px; width: 720px; height: 430px;
    border-radius: 28px; overflow: hidden;
    box-shadow: 0 6px 18px rgba(0,0,0,0.18);
  }
  /* Front */
  .card--front { top: 45px; background: var(--navy); }
  .card--front .swoosh { position: absolute; inset: 0; width: 100%; height: 100%; }
  .brand {
    position: absolute; display: flex; flex-direction: column; align-items: center;
  }
  .brand__square { width: 62px; height: 62px; }
  .brand__name {
    font-family: "Cinzel", Georgia, serif; font-weight: 400;
    letter-spacing: 0.06em; white-space: nowrap;
  }
  .card--front .brand { right: 60px; top: 95px; }
  .card--front .brand__square { background: var(--paper); margin-bottom: 22px; }
  .card--front .brand__name { color: var(--paper); font-size: 46px; }
  .card--front .website {
    margin-top: 34px; color: var(--paper); font-size: 19px; font-weight: 500; letter-spacing: 0.03em;
  }
  /* Back */
  .card--back { top: 525px; background: var(--paper); }
  .edge-band { position: absolute; left: 0; top: 0; bottom: 0; width: 16px; background: var(--navy); }
  .card--back .brand { left: 58px; top: 36px; align-items: center; }
  .card--back .brand__square { background: var(--navy); margin-bottom: 16px; width: 54px; height: 54px; }
  .card--back .brand__name { color: var(--ink); font-size: 38px; }
  .contact { position: absolute; left: 64px; top: 196px; color: var(--text); }
  .contact__name { color: var(--navy); font-size: 27px; font-weight: 700; letter-spacing: 0.01em; }
  .contact__role { font-size: 19px; margin-top: 2px; margin-bottom: 12px; }
  .contact__line { font-size: 18px; line-height: 1.45; display: flex; align-items: center; gap: 6px; }
  .label { color: var(--navy); }
  .icon-mail { width: 16px; height: 12px; }
  .footer-web {
    position: absolute; right: 70px; bottom: 46px; font-size: 18px; color: var(--ink); letter-spacing: 0.02em;
  }
  .footer-web strong { color: var(--navy); font-weight: 700; }
  .footer-bar { position: absolute; right: 70px; bottom: 0; width: 210px; height: 34px; background: var(--navy); }
</style>
</head>
<body>
  <section class="card card--front">
    <svg class="swoosh" viewBox="0 0 720 430" preserveAspectRatio="none" aria-hidden="true">
      <path d="M0 0 H300 C360 70 330 150 250 190 C180 225 120 250 90 430 H0 Z" fill="var(--navy-deep)"/>
      <path d="M0 170 C70 150 150 170 230 190 C140 215 90 280 70 430 H0 Z" fill="#08123c" opacity="0.6"/>
    </svg>
    <div class="brand">
      <div class="brand__square"></div>
      <div class="brand__name">Quayvale Legal</div>
      <div class="website">www.qvlegal.com.au</div>
    </div>
  </section>

  <section class="card card--back">
    <div class="edge-band"></div>
    <div class="brand">
      <div class="brand__square"></div>
      <div class="brand__name">Quayvale Legal</div>
    </div>
    <div class="contact">
      <div class="contact__name">PAUL WHITCOMBE</div>
      <div class="contact__role">Managing Partner</div>
      <div class="contact__line">Level 9, 7 Ferris Lane Sydney NSW 2000</div>
      <div class="contact__line"><span class="label">Main Tel</span> 02 9364 2710</div>
      <div class="contact__line"><span class="label">Direct Tel</span> 02 8472 3159</div>
      <div class="contact__line">
        <svg class="icon-mail" viewBox="0 0 16 12" aria-hidden="true">
          <rect x="0.5" y="0.5" width="15" height="11" rx="1" fill="var(--navy)"/>
          <path d="M1 1.5 L8 7 L15 1.5" stroke="#fff" stroke-width="1.3" fill="none"/>
        </svg>
        paul@qvlegal.com.au
      </div>
    </div>
    <div class="footer-web">www.<strong>qvlegal.com</strong>.au</div>
    <div class="footer-bar"></div>
  </section>
</body>
</html>
```